Fruit Juice packaging for Canada Market

We need label designs for our Fruit juice in PET form and we have 6 flavours ( tamarind, Blueberry, Passion Fruit+ Mango, Cucumis Melo+green tea, Mulberry, and Mango.
We need designs for packaging for all 6 listed fruits

1) Blueberry Juice labeling.
2) Tamarind Juice labeling.
3) Mulberry Juice labeling.
4) Passion fruit + Mango Juice labeling.
5) Cucumis Melo+green tea Juice labeling.
6) Mango Juice labeling.

A: PET bottle shape and dimensions:
- Dimensions: please refer to attachment name: REVIMO Bottle shape
- Bottle shape: Please refer to attachment name: BOTTLE SHAPE for the actual look of the bottle design.

B: Design Ideal: we want to have a look of fresh and juicy of real fruits since we are producing RAW juices. You can chose any taken photo of fruits on Pixdrawer. (http://www.pixdrawer-example.com/photos/blueberry?phrase=Blueberry&excludenudity=true&sort=best)

C: Fonts will be up to the designer choose, easy to read, neat and easy recognize

D: Label content needs to have followings: please refer to attachment REVIMO SAMPLE DESIGN for all needed information.
Main licence Company: HALVERN Trading Inc.
Product Name: REVIMO
Product Name1 : Revimo Blueberry Juice (attached)
Flavor Name 1 : Blueberry
and
Product Name 2 : Revimo Tamarind Juice (attached)
Flavor Name 2: Tamarind
...and so on for the rest of juices

I want the design in English with editable Ai or PTS so that I can add shortly Vietnamese translation text as mandatory law in our current market-Vietnam. We will take care the translation for you.

Old labels are attached to give you an idea. Contents in the old will be pasted in your labels (nutrition facts, net weight, ingredient, direction of use... etc). you re-design to make it fresher and healthier.

On the label for 330ml PET bottle, (please see picture of sample bottle), decal dimension of L:17.5cm x H:12cm following phrase must be included:

- Made of Real Fruit Juice

- Direction of use: will be provided in Ai.
- Ingredients: will be provided in Ai.

- Production and Packaging under licence of
DORUPE INC., CANADA
482 Tremblant Ouest, Quebec, CANADA.

- Importing, Producing and Distributing by BENOSU Ltd.,
- Km7, Lac Vien city, Ho Chi Minh, Viet Nam.
- Made in Vietnam

- Nutrition Fact ( Canada label requirements)
- HALAL logo ( will be provided, show at front and on the back)
- ISO 22000:2005 logo (will be provided )
-Manufacturing date/Used by date: on the cap.
-Keep refrigerated for an even better taste.

(Somewhere in Front)

0% Cholesterol
Blueberry imports from CANADA. (for Blueberry Juice)
Delicious Tamarind from VIETNAM. ( for Tamarind juice)
Has HALAL logo at front ( see provided picture for reference)
picture of juice, fresh, wet fruits around the bottom bottle.
running juice from the juice at the bottom to the cap.

(P/S: the label packaging must meet the standard requirement for Canada)
Please request me for more info if needed.

Target Market(s)

VIETNAM and NORTH AMERICA

Industry/Entity Type

Pet

Font styles to use
Serif
Sans Serif
Decorative
Script
Other font styles liked:
• Prefer to designers to chose on their design to make it looks match

Colors

Designer to choose colors to be used in the design.

Requirements
Must have
• meet Canada Labeling requirement for imported products.
• Ai editable version is a must to allow us to add Vietnamese translation and movable objects on the packaging design after we add Vietnamese text.
Nice to have
• have done any packaging with Canadian customers with Nutrition Facts on.

```html
<!DOCTYPE html>
<html lang="en">
<head>
<meta charset="UTF-8">
<title>Revimo Blueberry Juice – Label</title>
<link rel="stylesheet" href="https://fonts.googleapis.com/css2?family=Montserrat:wght@500;600&family=Playfair+Display:wght@400&display=swap">
<style>
  :root {
    --page-bg: #e4e6ea;
    --berry-deep: #3f5a86;
    --berry-mid: #6f87b2;
    --berry-light: #a9b9d6;
    --label-text: #f4f6fa;
    --brand-red: #e0334f;
  }
  * { margin: 0; padding: 0; box-sizing: border-box; }
  html, body {
    width: 1200px;
    height: 1200px;
    overflow: hidden;
    background: var(--page-bg);
  }
  .canvas {
    width: 1200px;
    height: 1200px;
    display: flex;
    align-items: center;
    justify-content: center;
  }
  .label {
    position: relative;
    width: 1050px;
    height: 720px;
    overflow: hidden;
    border-radius: 6px;
    box-shadow: 0 10px 40px rgba(40, 55, 90, 0.18);
  }
  .label__photo {
    position: absolute;
    inset: 0;
    background:
      radial-gradient(circle at 22% 30%, var(--berry-light) 0, transparent 28%),
      radial-gradient(circle at 70% 62%, var(--berry-light) 0, transparent 30%),
      radial-gradient(circle at 45% 85%, var(--berry-mid) 0, transparent 35%),
      linear-gradient(160deg, var(--berry-mid) 0%, var(--berry-deep) 55%, #34496e 100%);
  }
  .label__content {
    position: relative;
    height: 100%;
    display: flex;
    flex-direction: column;
    align-items: center;
    padding-top: 70px;
    text-align: center;
    color: var(--label-text);
  }
  .brand {
    font-family: "Montserrat", sans-serif;
    font-weight: 600;
    font-size: 58px;
    letter-spacing: 1px;
    color: var(--brand-red);
    display: flex;
    align-items: center;
    gap: 14px;
  }
  .brand__mark {
    width: 18px;
    height: 18px;
    background: var(--brand-red);
  }
  .product-name {
    font-family: "Playfair Display", serif;
    font-weight: 400;
    line-height: 0.95;
    margin-top: 60px;
    text-shadow: 0 2px 6px rgba(20, 30, 60, 0.35);
  }
  .product-name__flavour { display: block; font-size: 120px; }
  .product-name__type { display: block; font-size: 110px; }
  .claim {
    font-family: "Montserrat", sans-serif;
    font-weight: 500;
    font-size: 22px;
    letter-spacing: 4px;
    line-height: 1.35;
    text-transform: uppercase;
    margin-top: 48px;
  }
  .net-volume {
    font-family: "Montserrat", sans-serif;
    font-weight: 600;
    font-size: 22px;
    letter-spacing: 4px;
    text-transform: uppercase;
    position: absolute;
    bottom: 36px;
  }
</style>
</head>
<body>
  <main class="canvas">
    <section class="label">
      <div class="label__photo" role="img" aria-label="Close-up photograph of fresh wet blueberries covered in water droplets"></div>
      <div class="label__content">
        <div class="brand"><span class="brand__mark"></span>Revimo</div>
        <h1 class="product-name">
          <span class="product-name__flavour">Blueberry</span>
          <span class="product-name__type">Juice</span>
        </h1>
        <p class="claim">Made with<br>real fruit juice<br>from blueberries<br>imported<br>from Canada</p>
        <p class="net-volume">Net volume: 330ml</p>
      </div>
    </section>
  </main>
</body>
</html>
```